Stationery Design Project

We need a stationery design for our Norwegian trucking company. We have existed for about 15 years and our 12 drivers uses relatively new vehicles to transport goods around in northern Norway. Long distance routes with fresh fish og food transport is our main operations.

We have already made alogo that's printed on our trucks. The logo and a picture of our trucks is attached. I think the logo i crappy, but since its already in use, changing it is not an option in this round. Still using a better colour scheme in the overall stationery and more interesting fonts is possible (altso in the logo).

Company details:
Name: Kjelvraket AS
Organisation nr 873 615 309
Post adress: 8642 Raudvik

I like minimalism and simplicity. I am avalibly for questions in normal GMT working hours either here or on mail: ivar@fjordlast.no

Reason: Hi. Im extending the deadline because I needed some time to find a vector file of our logo. Sorry for the inconvenience

Hi, and thanks for all your interest in the project. Some updates:

-          I have decided to commit to using one of the designs. Some designer will get the payment.

-          I have extended the deadline with 24 hours since I needed some time to find our firms vector logo (a slow Swedish man was holding me up)

-          We will not choose a design before the deadline. No need to rush.

-          We have received a lot of great design and think there is a need to specified the product we want to make:

o   Business Card for all our employers. I just need the design and will duplicate with the correct numbers and name myself. The information on should be: Logo, employer’s name, Phone number, email, website, Postal number and address. Use this as a template: logo, Leif Brattvoll, 47382066, Leif@fjordlast.no,, fjordlast.no, 8642 Raudvik. The order and placement of the information is your creative decision.

o   Stickers to put on the goods we travel. On the sticker the should be the following information: Logo, phone number, Tekst and link: Fraktæ av Kjelvraket. Ke du syns? Fjordlast.no/tilbakemelding (this means: Handled by Kjelvraket. What do you think Fjordlast.no/feedback -à the link will be a feedback form). The placement the information and size is your creative decision with some stings: we have been thinking of using Drukko for printing and see that a size about 6x6 cm, 8x5 or something like that. (with 3000 copies our budget is 200 punds). Any suggestions of other suppliers are welcome. Drukko price calculator http://www.drukkolabelhouse.co.uk/digital-litho-printing/printing-labels-tags/stickers/

o   Letterhead with logo, address, phone number and organizational number.

o   Envelopes with logo,address, phone number and organizational number.

Have a nice day.

 

 

• Using the blue colour in the logo and using a similar graphic approch.

```html
<!DOCTYPE html>
<html lang="no">
<head>
<meta charset="utf-8">
<title>Kjelvraket AS – stationery set</title>
<link rel="stylesheet" href="https://fonts.googleapis.com/css2?family=Open+Sans:wght@400;600;700&family=Arimo:wght@400&display=swap">
<style>
  :root{
    --brand:#1d50ad;
    --brand-soft:#dfe6f1;
    --ink:#222;
    --muted:#666;
    --paper:#fff;
    --stage:#1f2024;
    --card-dark:#1b1b1b;
    --sans:"Open Sans", Arial, sans-serif;
    --form:"Arimo", Arial, sans-serif;
  }
  *{margin:0;padding:0;box-sizing:border-box}
  html,body{width:1200px;height:665px;overflow:hidden;background:var(--stage)}
  .stage{position:relative;width:1200px;height:665px;font-family:var(--sans);color:var(--ink)}
  .piece{position:absolute;background:var(--paper);overflow:hidden;box-shadow:0 3px 10px rgba(0,0,0,.6)}
  .wave{position:absolute;left:0;bottom:0;width:100%;color:var(--brand)}
  .logo{position:absolute;display:flex;align-items:center;gap:4px;font-weight:700;color:var(--brand);white-space:nowrap;line-height:1}
  .logo .dot{display:block;border-radius:50%;background:currentColor}
  .logo-lg{font-size:21px}.logo-lg .dot{width:12px;height:12px}
  .logo-sm{font-size:12px}.logo-sm .dot{width:7px;height:7px}
  .logo-xs{font-size:9px}.logo-xs .dot{width:5px;height:5px}
  .logo-white{color:#fff}
  .addr{position:absolute;font-size:7.5px;line-height:10px}
  .addr.right{text-align:right}
  .contact{position:absolute;color:#fff;font-size:7px;line-height:8.5px}

  /* sheets */
  .sheet{width:339px;height:438px;top:25px}
  .fax{left:27px}
  .letter{left:401px}
  .fax-title{position:absolute;left:22px;top:76px;font-family:var(--form);font-size:20px;font-weight:400}
  .fax-row{position:absolute;left:22px;width:290px;height:12px;border-bottom:1px solid #444;font-family:var(--form);font-size:6.5px;display:flex}
  .fax-row span{flex:0 0 156px}
  .fax-checks{position:absolute;left:22px;top:183px;width:292px;display:flex;justify-content:space-between;font-family:var(--form);font-size:6.5px}
  .fax-checks span{display:flex;align-items:center;gap:4px}
  .fax-checks i{display:block;width:7px;height:7px;background:#bbb}
  .letter-mark{position:absolute;left:60px;top:193px;font-size:40px;font-weight:700;color:var(--brand-soft)}

  /* envelopes */
  .env-dl{left:788px;top:28px;width:379px;height:163px}
  .env-flap{position:absolute;left:792px;top:210px;width:376px;height:44px;color:var(--brand)}
  .env-flap .logo{left:160px;top:17px;transform:rotate(180deg)}
  .env-open{left:790px;top:270px;width:380px;height:210px;background:transparent;box-shadow:none;overflow:visible}
  .env-open .body{position:absolute;left:0;top:0;width:380px;height:210px;background:var(--paper);border-radius:10px 10px 0 0;box-shadow:0 3px 10px rgba(0,0,0,.6);overflow:hidden}
  .env-open .flap-line{position:absolute;left:0;top:44px;width:380px;height:1px;background:#e4e4e4}
  .env-open .web{position:absolute;left:16px;bottom:9px;color:#fff;font-size:7px;letter-spacing:2.6px}

  /* cards */
  .card{top:523px;width:150px;height:86px;border-radius:6px}
  .card-front{left:31px}
  .card-back{left:196px}
  .card-dark{left:364px;background:var(--card-dark)}
  .card .name{position:absolute;left:104px;top:19px;font-size:5.5px;line-height:7px;white-space:nowrap}
  .card .name small{display:block;font-size:4px;line-height:6px;color:var(--muted)}
  .card .foot{position:absolute;left:6px;bottom:4px;color:#fff;font-size:4.5px;line-height:6px}
  .card .web{position:absolute;left:0;width:100%;bottom:9px;text-align:center;font-size:4.5px;letter-spacing:1.5px;color:#888}

  /* stickers */
  .sticker{top:523px;width:126px;height:95px;border-radius:6px}
  .sticker-white{left:561px}
  .sticker-blue{left:703px;background:var(--brand)}
  .sticker-round{left:848px;top:527px;width:95px;height:95px;border-radius:50%}
  .sticker .msg{position:absolute;left:0;width:100%;text-align:center;color:var(--brand);font-size:8.5px;line-height:10.5px}
  .sticker-blue .msg{color:#fff}
  .sticker .tiny{position:absolute;left:6px;bottom:3px;font-size:4.5px;line-height:5.5px;color:#fff}
  .sticker-blue .tiny{color:var(--brand)}
  .sticker-round .msg{font-size:6.5px;line-height:8px}
  .sticker-round .tiny{left:0;width:100%;text-align:center;bottom:11px;font-size:3.6px;line-height:4.5px}
</style>
</head>
<body>
<svg width="0" height="0" style="position:absolute" aria-hidden="true">
  <symbol id="swoosh" viewBox="0 0 340 60" preserveAspectRatio="none">
    <path fill="currentColor" d="M0,3 C110,0 230,6 340,12 L340,60 L0,60 Z"/>
    <path fill="none" stroke="#fff" stroke-width="5" d="M0,9 C120,5 230,14 340,38"/>
    <path fill="none" stroke="#1a1a1a" stroke-width="2" d="M0,13 C120,9 230,18 340,42"/>
  </symbol>
</svg>

<main class="stage">

  <section class="piece sheet fax">
    <div class="logo logo-lg" style="left:22px;top:30px"><span class="dot"></span>Kjelvraket</div>
    <p class="addr right" style="right:26px;top:45px">8642 Raudvik.<br>Org. nr. 873 615 309</p>
    <h1 class="fax-title">FAX</h1>
    <div class="fax-row" style="top:103px"><span>To :</span>From :</div>
    <div class="fax-row" style="top:121px"><span>Fax :</span>Page:</div>
    <div class="fax-row" style="top:139px"><span>Phone :</span>Date:</div>
    <div class="fax-row" style="top:157px"><span>Re :</span>CC:</div>
    <div class="fax-checks">
      <span><i></i>Urgent</span><span><i></i>For Review</span><span><i></i>Please Comment</span><span><i></i>Please Reply</span><span>Please Recycle</span>
    </div>
    <svg class="wave" height="50"><use href="#swoosh"/></svg>
    <p class="contact" style="left:22px;bottom:5px">phone : 47382066<br>email : Leif@fjordlast.no<br>web : www.fjordlast.no</p>
  </section>

  <section class="piece sheet letter">
    <div class="logo logo-lg" style="left:22px;top:30px"><span class="dot"></span>Kjelvraket</div>
    <p class="addr right" style="right:26px;top:45px">8642 Raudvik.<br>Org. nr. 873 615 309</p>
    <div class="letter-mark">Kjelvraket</div>
    <svg class="wave" height="50"><use href="#swoosh"/></svg>
    <p class="contact" style="left:22px;bottom:5px">phone : 47382066<br>email : Leif@fjordlast.no<br>web : www.fjordlast.no</p>
  </section>

  <section class="piece env-dl">
    <div class="logo logo-lg" style="left:13px;top:22px"><span class="dot"></span>Kjelvraket</div>
    <p class="addr" style="left:13px;top:57px">8642 Raudvik.<br>Org. nr. 873 615 309</p>
    <svg class="wave" height="50"><use href="#swoosh"/></svg>
    <p class="contact" style="left:13px;bottom:4px">phone : 47382066<br>email : Leif@fjordlast.no<br>web : www.fjordlast.no</p>
  </section>

  <div class="env-flap">
    <svg width="376" height="44" viewBox="0 0 376 44"><path fill="currentColor" d="M10,0 H366 L376,34 Q376,44 366,44 H10 Q0,44 0,34 Z"/></svg>
    <div class="logo logo-xs logo-white"><span class="dot"></span>Kjelvraket</div>
  </div>

  <section class="piece env-open">
    <div class="body">
      <div class="flap-line"></div>
      <div class="logo logo-xs" style="left:162px;top:16px;transform:rotate(180deg)"><span class="dot"></span>Kjelvraket</div>
      <div class="logo logo-lg" style="left:14px;top:70px"><span class="dot"></span>Kjelvraket</div>
      <p class="addr" style="left:16px;top:104px">8642 Raudvik.<br>Org. nr. 873 615 309</p>
      <svg class="wave" height="50"><use href="#swoosh"/></svg>
      <p class="web">www.fjordlast.no</p>
    </div>
  </section>

  <section class="piece card card-front">
    <div class="logo logo-sm" style="left:8px;top:18px"><span class="dot"></span>Kjelvraket</div>
    <p class="name">Leif Brattvoll<small>47382066<br>Leif@fjordlast.no<br>www.fjordlast.no</small></p>
    <svg class="wave" height="30"><use href="#swoosh"/></svg>
    <p class="foot">8642 Raudvik.<br>Organization nr 873 615 309</p>
  </section>
  <section class="piece card card-back">
    <div class="logo logo-sm" style="left:34px;top:34px"><span class="dot"></span>Kjelvraket</div>
    <p class="web">www.fjordlast.no</p>
  </section>
  <section class="piece card card-dark">
    <div class="logo logo-sm" style="left:34px;top:34px"><span class="dot"></span>Kjelvraket</div>
    <p class="web">www.fjordlast.no</p>
  </section>

  <section class="piece sticker sticker-white">
    <div class="logo logo-sm" style="left:16px;top:11px"><span class="dot"></span>Kjelvraket</div>
    <p class="msg" style="top:36px">Tekst and link<br>Fraktae av Kjelvraket<br>Ke du syns?</p>
    <svg class="wave" height="26"><use href="#swoosh"/></svg>
    <p class="tiny">Fjordlast.no/tilbakemelding<br>phone : 47382066</p>
  </section>
  <section class="piece sticker sticker-blue">
    <div class="logo logo-sm logo-white" style="left:16px;top:11px"><span class="dot"></span>Kjelvraket</div>
    <p class="msg" style="top:36px">Tekst and link<br>Fraktae av Kjelvraket<br>Ke du syns?</p>
    <svg class="wave" height="26" style="color:#fff"><use href="#swoosh"/></svg>
    <p class="tiny">Fjordlast.no/tilbakemelding<br>phone : 47382066</p>
  </section>
  <section class="piece sticker sticker-round">
    <div class="logo logo-xs" style="left:20px;top:20px"><span class="dot"></span>Kjelvraket</div>
    <p class="msg" style="top:34px">Tekst and link<br>Fraktae av Kjelvraket<br>Ke du syns?</p>
    <svg class="wave" height="32"><use href="#swoosh"/></svg>
    <p class="tiny">Fjordlast.no/tilbakemelding<br>phone : 47382066</p>
  </section>

</main>
</body>
</html>
```